Business cards for Harbourline Supply Pty Ltd that import building products into Australia from China
Target Market(s)
Business to Business
Industry/Entity Type
Business
Contact Information for Business Card
Front: Logo and Business Name
Rear:
Desmond Varrick
General Manager
Mobile: 0427 561 394
email: dessie@harbourlinesupply.com.au
alternative email: dessie@outbackworks.com.au
web: www.harbourlinesupply.com.au
Adelaide, Brisbane and Darwin
Colors
ec1f27
fbee3d

```html
<!DOCTYPE html>
<html lang="en">
<head>
<meta charset="utf-8">
<title>Harbourline Supply Pty Ltd — Business Cards</title>
<link rel="stylesheet" href="https://fonts.googleapis.com/css2?family=Montserrat:wght@400;500;700&display=swap">
<style>
  :root {
    --brand-red: #ec1f27;
    --brand-yellow: #fbee3d;
    --card-black: #050505;
    --card-white: #ffffff;
    --ink-grey: #3a3a3a;
    --page-bg: #2b2b2b;
  }
  * { box-sizing: border-box; margin: 0; padding: 0; }
  html, body {
    width: 1200px; height: 864px; overflow: hidden;
    background: var(--page-bg);
    font-family: "Montserrat", sans-serif;
  }
  .sheet {
    width: 1200px; height: 864px;
    display: flex; flex-direction: column; align-items: center; justify-content: center;
    gap: 36px;
  }
  .card {
    position: relative;
    width: 640px; height: 366px;
    border-radius: 22px;
    overflow: hidden;
    box-shadow: 0 14px 30px rgba(0,0,0,.45);
  }
  .card--front { background: var(--card-black); }
  .card--back { background: var(--card-white); }

  .wordmark {
    display: flex; align-items: center; gap: 14px;
    color: var(--brand-red);
    font-weight: 700;
    letter-spacing: .06em;
    text-transform: uppercase;
    white-space: nowrap;
  }
  .wordmark__dot {
    width: 16px; height: 16px; border-radius: 50%;
    background: var(--brand-red);
    flex: none;
  }
  .card--front .wordmark {
    position: absolute; top: 146px; left: 0; right: 0;
    justify-content: center;
    font-size: 27px;
  }
  .cities {
    position: absolute; bottom: 54px; left: 0; right: 0;
    text-align: center;
    color: #fff; font-size: 14px; font-weight: 500; letter-spacing: .02em;
  }
  .cities .sep { color: var(--brand-red); margin: 0 6px; }

  .card--back .wordmark {
    position: absolute; top: 72px; left: 0; right: 0;
    justify-content: center;
    font-size: 25px;
  }
  .person {
    position: absolute; left: 60px; top: 232px;
    width: 240px; text-align: right;
  }
  .person__name {
    color: var(--brand-red); font-size: 28px; font-weight: 500; line-height: 1.1;
  }
  .person__title {
    color: var(--ink-grey); font-size: 15px; margin-top: 6px;
  }
  .divider {
    position: absolute; left: 322px; top: 218px;
    width: 1px; height: 100px; background: #555;
  }
  .contact {
    position: absolute; left: 340px; top: 218px;
    list-style: none;
    color: var(--ink-grey); font-size: 13.5px;
  }
  .contact li {
    display: flex; align-items: center; gap: 10px;
    height: 25px;
  }
  .contact svg { width: 14px; height: 14px; flex: none; }
</style>
</head>
<body>
<main class="sheet">
  <section class="card card--front" aria-label="Card front">
    <div class="wordmark"><span class="wordmark__dot"></span>Harbourline Supply Pty Ltd</div>
    <p class="cities">Adelaide<span class="sep">•</span>Brisbane<span class="sep">•</span>Darwin</p>
  </section>

  <section class="card card--back" aria-label="Card back">
    <div class="wordmark"><span class="wordmark__dot"></span>Harbourline Supply Pty Ltd</div>

    <div class="person">
      <p class="person__name">Desmond Varrick</p>
      <p class="person__title">General Manager</p>
    </div>
    <div class="divider"></div>

    <ul class="contact">
      <li>
        <svg viewBox="0 0 14 14" aria-hidden="true"><rect x="3.5" y="1" width="7" height="12" rx="1.5" fill="none" stroke="var(--brand-red)" stroke-width="1.4"/><circle cx="7" cy="11" r=".8" fill="var(--brand-red)"/></svg>
        0427 561 394
      </li>
      <li>
        <svg viewBox="0 0 14 14" aria-hidden="true"><rect x="1" y="3" width="12" height="8" fill="var(--brand-red)"/><path d="M1 3 L7 8 L13 3" fill="none" stroke="#fff" stroke-width="1.1"/></svg>
        dessie@harbourlinesupply.com.au
      </li>
      <li>
        <svg viewBox="0 0 14 14" aria-hidden="true"><rect x="1" y="3" width="12" height="8" fill="var(--brand-red)"/><path d="M1 3 L7 8 L13 3" fill="none" stroke="#fff" stroke-width="1.1"/></svg>
        dessie@outbackworks.com.au
      </li>
      <li>
        <svg viewBox="0 0 14 14" aria-hidden="true"><g fill="none" stroke="var(--brand-red)" stroke-width="1.2"><circle cx="7" cy="7" r="5.8"/><ellipse cx="7" cy="7" rx="2.6" ry="5.8"/><path d="M1.2 7 H12.8 M2 4 H12 M2 10 H12"/></g></svg>
        www.harbourlinesupply.com.au
      </li>
    </ul>
  </section>
</main>
</body>
</html>
```